The design should look similar to the uploaded example to accommodate the information needed for a business card template. I would like to see the colors orange and charcoal grey incorporated along with the logo.The following should be on the back of the card SPECIALIZING IN NEW AND USED TIRES & WHEELS FOR:- Loaders- Skid Steers- Telehandlers- Boom Lifts- Forklifs and moreELIMINATING DOWNTIMEWheel Exchange Program for New & Used Foam Filled and Solid Rubber TiresSPECIALTY SERVICES- Foam Filling Tires- Largest Tire Press in SE- ONSITE Forklift Tire Press- Boom Truck Services - Rubber Tracks

Target Market(s)

New and Existing Customers

Industry/Entity Type

Business

Contact Information for Business Card

NAMEHEAVY DUTY TIRE, LLC8470 Belvedere RoadWest Palm Beach, FL 33411P: 844-HD-TIRESF: 561-431-6469C:E: W: WWW.GRANITERIMSUPPLY-EXAMPLE.COM

Font styles to use
Sans Serif

Colors
f37122
333333

Requirements
Must have
• The logo and the information indicated for the backside of the card
Nice to have
• Keep the orange and charcoal grey colors

```html
<!DOCTYPE html>
<html lang="en">
<head>
<meta charset="utf-8">
<title>Granite Rim Supply – Business Card</title>
<link rel="stylesheet" href="https://fonts.googleapis.com/css2?family=Open+Sans:wght@400;600;700&display=swap">
<style>
  :root{
    --orange:#f37122;
    --orange-card:#f8863a;
    --charcoal:#333333;
    --ink:#1c1c1c;
    --paper:#ffffff;
    --backdrop:#2a2b2e;
  }
  *{box-sizing:border-box;margin:0;padding:0}
  html,body{width:1200px;height:864px;overflow:hidden}
  body{background:var(--backdrop);font-family:"Open Sans",Arial,sans-serif;position:relative}
  .card{position:absolute;left:310px;width:580px;height:330px;overflow:hidden}
  .card--services{top:72px;background:var(--paper);color:var(--ink)}
  .card--contact{top:462px;background:var(--orange-card);color:var(--paper)}

  /* services side */
  .brand-mark{position:absolute;left:34px;top:34px;display:flex;align-items:center;gap:10px}
  .brand-mark__dot{width:42px;height:42px;border-radius:50%;background:var(--charcoal)}
  .brand-mark__name{font-weight:700;font-size:16px;line-height:1.1;color:var(--charcoal)}
  .headline{position:absolute;left:210px;top:40px}
  .headline__kicker{color:var(--orange);font-weight:700;font-size:14px;letter-spacing:.2px}
  .headline__text{font-weight:600;font-size:15px;line-height:1.3;color:var(--ink)}
  .services{position:absolute;left:0;top:140px;width:270px;text-align:right;padding-right:22px}
  .equipment{position:absolute;left:300px;top:140px;width:260px}
  .col-title{color:var(--orange);font-weight:700;font-size:15px;line-height:1.25;margin-bottom:8px}
  .list{list-style:none;font-weight:600;font-size:13.5px;line-height:1.45}
  .services .list li::after,.equipment .list li::before{content:"";display:inline-block;width:6px;height:6px;border-radius:50%;background:var(--orange);vertical-align:middle}
  .services .list li::after{margin-left:8px}
  .equipment .list li::before{margin-right:7px}
  .divider{position:absolute;left:283px;top:150px;width:2px;height:125px;background:var(--orange)}

  /* contact side */
  .person{position:absolute;left:40px;top:36px}
  .person__name{font-weight:700;font-size:20px}
  .person__company{font-weight:600;font-size:15px;margin-top:14px}
  .person__address{font-size:14px;line-height:1.45;margin-top:2px}
  .contacts{position:absolute;left:40px;top:178px;list-style:none;font-size:14px;line-height:1.5}
  .contacts li{display:flex;align-items:center;gap:12px}
  .contacts svg{width:12px;height:12px;fill:var(--paper)}
  .logo-block{position:absolute;right:40px;top:50px;width:190px;display:flex;flex-direction:column;align-items:center;gap:14px}
  .logo-block__dot{width:150px;height:150px;border-radius:50%;background:var(--charcoal)}
  .logo-block__name{font-weight:700;font-size:22px;color:var(--charcoal);letter-spacing:.5px}
</style>
</head>
<body>

<section class="card card--services" aria-label="Card back: services">
  <div class="brand-mark">
    <span class="brand-mark__dot"></span>
    <span class="brand-mark__name">GRANITE<br>RIM</span>
  </div>
  <div class="headline">
    <p class="headline__kicker">ELIMINATING DOWNTIME</p>
    <p class="headline__text">Wheel Exchange Program for New &amp;<br>Used Foam Filled and Solid Rubber Tires</p>
  </div>
  <div class="services">
    <h2 class="col-title">SPECIALTY SERVICES</h2>
    <ul class="list">
      <li>Foam Filling Tires</li>
      <li>Largest Tire Press in SE</li>
      <li>ONSITE Forklift Tire Press</li>
      <li>Boom Truck Services</li>
      <li>Rubber Tracks</li>
    </ul>
  </div>
  <span class="divider"></span>
  <div class="equipment">
    <h2 class="col-title">SPECIALIZING IN NEW AND<br>USED TIRES &amp; WHEELS FOR:</h2>
    <ul class="list">
      <li>Loaders</li>
      <li>Skid Steers</li>
      <li>TelehandlersBoom Lifts</li>
      <li>Forklifs and more</li>
    </ul>
  </div>
</section>

<section class="card card--contact" aria-label="Card front: contact details">
  <div class="person">
    <p class="person__name">Daniel Whitcombe</p>
    <p class="person__company">GRANITE RIM SUPPLY, LLC</p>
    <p class="person__address">5126 Marston Lane<br>Coral Bend, FL 33490</p>
  </div>
  <ul class="contacts">
    <li><svg viewBox="0 0 12 12"><path d="M2.5 0.5l2 2.5-1.2 1.3c.8 1.7 2 2.9 3.4 3.6L8 6.6l2.5 2-1 2.4C5 10.5 1.5 7 0.5 2z"/></svg>844-GR-WHEEL</li>
    <li><svg viewBox="0 0 12 12"><path d="M3 0h5v3H3zM0 4h12v6H9v2H3v-2H0zM4 8v3h4V8z"/></svg>561-278-9053</li>
    <li><svg viewBox="0 0 12 12"><path d="M3 0h6v12H3zM4 1.5v8h4v-8z"/></svg>561-000-0000</li>
    <li><svg viewBox="0 0 12 12"><path d="M0 2h12v1L6 7 0 3zM0 4.5l6 4 6-4V10H0z"/></svg>info@granite-example.com</li>
    <li><svg viewBox="0 0 12 12"><circle cx="6" cy="6" r="6"/></svg>www.graniterimsupply-example.com</li>
  </ul>
  <div class="logo-block">
    <span class="logo-block__dot"></span>
    <span class="logo-block__name">GRANITE RIM</span>
  </div>
</section>

</body>
</html>
```